Velmarotix - world unique technology for better life - please let them know who am i at first sight

We need a new business card for company which is a provider of unique crystal based technology suitable for all living being. For more information and final design you can use our brochure (our colours are black and blue from brochure).
We use Verdana font

Industry/Entity Type

Business

Contact Information for Business Card

regular dimension

Font styles to use
Other font styles liked:
• Verdana

Requirements
Must have
• Logo
• name
• function/position
• phone
• mobile
• e-mail
• adress
Nice to have
• inovative design (technology directed)

```html
<!DOCTYPE html>
<html lang="en">
<head>
<meta charset="utf-8">
<title>Velmarotix business card</title>
<link href="https://fonts.googleapis.com/css2?family=Lato:wght@300;400&display=swap" rel="stylesheet">
<style>
  :root {
    --page-bg: #e7e4df;
    --card-bg: #ffffff;
    --card-shadow: rgba(40, 30, 20, 0.18);
    --brand-blue: #1fb3de;
    --ink: #1b1b1b;
    --icon-bg: #111111;
  }
  * { box-sizing: border-box; margin: 0; padding: 0; }
  html, body { width: 1200px; height: 858px; overflow: hidden; }
  body {
    background: var(--page-bg);
    font-family: "Lato", Verdana, sans-serif;
    position: relative;
  }
  .card {
    position: absolute;
    width: 540px;
    height: 309px;
    background: linear-gradient(160deg, #ffffff 0%, #f4f4f4 100%);
    box-shadow: 0 10px 28px var(--card-shadow), 0 2px 4px rgba(0,0,0,0.08);
    top: 274px;
  }
  .card--front { left: 40px; }
  .card--back  { left: 620px; }

  .brand { position: absolute; display: flex; align-items: center; gap: 12px; }
  .brand__mark {
    width: 46px; height: 46px; border-radius: 50%;
    background: var(--brand-blue);
  }
  .brand__name {
    color: var(--brand-blue);
    font-weight: 300;
    font-size: 30px;
    letter-spacing: 1px;
  }
  .card--front .brand { left: 34px; top: 54px; }
  .card--back .brand { left: 110px; top: 92px; }
  .card--back .brand__mark { width: 62px; height: 62px; }
  .card--back .brand__name { font-size: 36px; }

  .holder { position: absolute; left: 40px; bottom: 46px; }
  .holder__name { font-size: 22px; font-weight: 400; color: var(--ink); }
  .holder__role { font-size: 14px; color: var(--brand-blue); margin-top: 3px; }

  .contact {
    position: absolute; left: 270px; top: 112px;
    list-style: none;
  }
  .contact__item {
    display: flex; align-items: center; gap: 8px;
    font-size: 12.5px; color: var(--brand-blue);
    height: 20px;
  }
  .contact__icon {
    width: 15px; height: 15px; background: var(--icon-bg);
    display: flex; align-items: center; justify-content: center;
    flex: none;
  }
  .contact__icon svg { width: 11px; height: 11px; }
  .contact__item--cont .contact__icon { background: none; }

  .social {
    position: absolute; left: 64px; bottom: 44px;
    display: flex; gap: 6px;
  }
  .social__box { width: 17px; height: 17px; background: var(--icon-bg); }
</style>
</head>
<body>
  <section class="card card--front" aria-label="Card front">
    <div class="brand">
      <span class="brand__mark"></span>
      <span class="brand__name">VELMAROTIX</span>
    </div>

    <ul class="contact">
      <li class="contact__item">
        <span class="contact__icon"><svg viewBox="0 0 12 12"><rect x="1" y="3" width="10" height="7" rx="1" fill="none" stroke="#1fb3de" stroke-width="1.3"/><rect x="4" y="1.5" width="4" height="2" fill="#1fb3de"/></svg></span>
        000-0000-0000
      </li>
      <li class="contact__item">
        <span class="contact__icon"><svg viewBox="0 0 12 12"><rect x="3.5" y="1" width="5" height="10" rx="1" fill="none" stroke="#1fb3de" stroke-width="1.3"/><circle cx="6" cy="9" r="0.7" fill="#1fb3de"/></svg></span>
        +385(0) 41 735 264
      </li>
      <li class="contact__item">
        <span class="contact__icon"><svg viewBox="0 0 12 12"><rect x="1" y="2.5" width="10" height="7" fill="none" stroke="#1fb3de" stroke-width="1.2"/><path d="M1 2.5 L6 7 L11 2.5" fill="none" stroke="#1fb3de" stroke-width="1.2"/></svg></span>
        info@velmarotix.eu
      </li>
      <li class="contact__item">
        <span class="contact__icon"><svg viewBox="0 0 12 12"><circle cx="6" cy="6" r="4.8" fill="none" stroke="#1fb3de" stroke-width="1.2"/><ellipse cx="6" cy="6" rx="2" ry="4.8" fill="none" stroke="#1fb3de" stroke-width="1"/><line x1="1.2" y1="6" x2="10.8" y2="6" stroke="#1fb3de" stroke-width="1"/></svg></span>
        www.velmarotix.eu
      </li>
      <li class="contact__item">
        <span class="contact__icon"><svg viewBox="0 0 12 12"><path d="M6 11 C3 7 2.5 5.5 2.5 4.5 A3.5 3.5 0 0 1 9.5 4.5 C9.5 5.5 9 7 6 11 Z" fill="#1fb3de"/><circle cx="6" cy="4.5" r="1.3" fill="#111"/></svg></span>
        82-90 Harrowfield Lane London
      </li>
      <li class="contact__item contact__item--cont">
        <span class="contact__icon"></span>
        EC2K 7QZ United Kingdom
      </li>
    </ul>

    <div class="holder">
      <p class="holder__name">Your Name</p>
      <p class="holder__role">Position</p>
    </div>
  </section>

  <section class="card card--back" aria-label="Card back">
    <div class="brand">
      <span class="brand__mark"></span>
      <span class="brand__name">VELMAROTIX</span>
    </div>
    <div class="social" aria-label="Social profiles">
      <span class="social__box"></span>
      <span class="social__box"></span>
      <span class="social__box"></span>
      <span class="social__box"></span>
      <span class="social__box"></span>
      <span class="social__box"></span>
    </div>
  </section>
</body>
</html>
```